Brightwater Care Partners, LLC Business Card update!

would like a classier business card. Our cards currently just have our logo and contact information. Need better use of color and creativity
Logo attached.

Target Market(s)

Potential clients, contacts, existing clients. We are a consulting company

Industry/Entity Type

Business

Contact Information for Business Card

We like our colors but just have a boring card with our logo and a white background. I want something that stands out.

Colors
ec1f27
757575

Requirements
Must have
• Color to stay consistent. Logo provided
Nice to have
• Just better use of color/ design

```html
<!DOCTYPE html>
<html lang="en">
<head>
<meta charset="utf-8">
<title>Brightwater Care Partners – Business Card</title>
<link href="https://fonts.googleapis.com/css2?family=Exo+2:wght@400;500&display=swap" rel="stylesheet">
<style>
  :root {
    --brand-red: #ec1f27;
    --brand-grey: #757575;
    --ink: #3a3a3a;
    --paper: #ffffff;
    --backdrop: #e8e8e8;
  }
  html, body {
    margin: 0;
    width: 1200px;
    height: 901px;
    overflow: hidden;
    background: var(--backdrop);
    font-family: "Exo 2", sans-serif;
  }
  .canvas {
    position: relative;
    width: 1200px;
    height: 901px;
  }
  .card {
    position: absolute;
    top: 300px;
    width: 525px;
    height: 300px;
    background: var(--paper);
    border-radius: 22px;
    overflow: hidden;
    box-shadow: 0 6px 18px rgba(0,0,0,0.12);
  }
  .card--front { left: 50px; }
  .card--back { left: 625px; }

  .card__bands {
    position: absolute;
    inset: 0;
  }

  .wordmark {
    position: absolute;
    display: flex;
    align-items: center;
    gap: 10px;
    color: var(--brand-red);
    font-weight: 500;
    letter-spacing: 0.5px;
    white-space: nowrap;
  }
  .wordmark__dot {
    border-radius: 50%;
    background: var(--brand-red);
    flex: none;
  }
  .card--front .wordmark {
    right: 40px;
    top: 120px;
    font-size: 19px;
  }
  .card--front .wordmark__dot { width: 18px; height: 18px; }
  .card--back .wordmark {
    left: 50%;
    top: 50%;
    transform: translate(-50%, -50%);
    font-size: 26px;
  }
  .card--back .wordmark__dot { width: 24px; height: 24px; }

  .holder {
    position: absolute;
    left: 190px;
    top: 40px;
    color: var(--ink);
  }
  .holder__name {
    margin: 0;
    font-size: 14px;
    font-weight: 500;
    letter-spacing: 1.5px;
  }
  .holder__title {
    margin: 3px 0 0;
    font-size: 10px;
    color: var(--brand-grey);
  }

  .contact {
    position: absolute;
    right: 30px;
    bottom: 26px;
    margin: 0;
    padding: 0;
    list-style: none;
    text-align: right;
    font-size: 10.5px;
    line-height: 17px;
    color: var(--ink);
  }
  .contact li {
    display: flex;
    justify-content: flex-end;
    align-items: center;
    gap: 7px;
  }
  .contact .contact__address { display: block; margin-bottom: 6px; line-height: 15px; }
  .contact svg { width: 10px; height: 10px; fill: var(--ink); flex: none; }
</style>
</head>
<body>
<main class="canvas">

  <section class="card card--front" aria-label="Business card front">
    <svg class="card__bands" viewBox="0 0 525 300" aria-hidden="true">
      <path d="M0 0 H200 C120 55 85 140 80 300 H0 Z" fill="var(--brand-grey)"/>
      <path d="M0 0 H152 C96 55 66 130 56 300 H0 Z" fill="var(--paper)"/>
      <path d="M0 0 H140 C88 55 58 130 46 300 H0 Z" fill="var(--brand-red)"/>
    </svg>

    <div class="holder">
      <p class="holder__name">DANIEL MERCER</p>
      <p class="holder__title">Managing Director</p>
    </div>

    <div class="wordmark">
      <span class="wordmark__dot"></span>
      <span>Brightwater Care Partners</span>
    </div>

    <ul class="contact">
      <li class="contact__address">214, 9th Floor Plaza<br>Harbor Road NWK</li>
      <li>012 555 0142
        <svg viewBox="0 0 10 10"><path d="M2 0.5 L3.8 2.6 L2.9 3.6 C3.5 5 4.9 6.4 6.4 7.1 L7.4 6.2 L9.5 8 L8.3 9.5 C4.5 9 1 5.5 0.5 1.7 Z"/></svg>
      </li>
      <li>012 555 0143
        <svg viewBox="0 0 10 10"><path d="M2.5 0 H7.5 V10 H2.5 Z M3.4 1 V8 H6.6 V1 Z" fill-rule="evenodd"/></svg>
      </li>
      <li>hello@brightwatercare.com
        <svg viewBox="0 0 10 10"><path d="M0 2 H10 V8.5 H0 Z M0.8 2.6 L5 5.6 L9.2 2.6 Z" fill-rule="evenodd"/></svg>
      </li>
      <li>www.brightwatercare.com
        <svg viewBox="0 0 10 10"><path d="M5 0 A5 5 0 1 0 5.01 0 Z M5 1.2 A3.8 3.8 0 1 1 4.99 1.2 Z" fill-rule="evenodd"/><path d="M4.4 0.5 H5.6 V9.5 H4.4 Z M0.5 4.4 H9.5 V5.6 H0.5 Z"/></svg>
      </li>
    </ul>
  </section>

  <section class="card card--back" aria-label="Business card back">
    <div class="wordmark">
      <span class="wordmark__dot"></span>
      <span>Brightwater Care Partners</span>
    </div>
  </section>

</main>
</body>
</html>
```